Cleaning service website design

We need a new nice web design(logo will be the same) for a new cleaning service Company:

Informations about Company and logo you can take from flyers in attachments.

This is a cleaning service Company which have simple rules and we would like to show that(in checklist form) on website:

- What we do and that we're Cleaning Green

- Why us?

- How much(our pricing is simple)

Also we would like to communicate with clients by some nice/big pictures on website and the most important thing is our phone number and short/fast Brimtallow.

Also there should be some space for description about our Company.

Generally all information on main page can be short: about us, about service(what we do), last reviews, tips (for example: Tip of the week) and other can be some introduction to subpage where will be more information.

There will be few subpages like: About us, About our service, Photos(Before and after), Reviews , Tips, FAQ, Contact, Looking for a Job? - most of them will be just text so you can project just one example.

```html
<!DOCTYPE html>
<html lang="en">
<head>
<meta charset="utf-8">
<title>Tidy Nest House Cleaning</title>
<link href="https://fonts.googleapis.com/css2?family=PT+Sans:ital,wght@0,400;0,700;1,400&family=PT+Sans+Narrow:wght@400;700&display=swap" rel="stylesheet">
<style>
:root{
  --green:#72bf5f;
  --green-dark:#4f8a1e;
  --green-panel:rgba(118,186,60,.88);
  --nav-blue:rgba(40,110,170,.72);
  --brand-blue:#1160a8;
  --deep-blue:#0a2e8a;
  --orange:#ffb400;
  --orange-dark:#e69500;
  --text:#333;
  --muted:#555;
  --white:#fff;
}
*{box-sizing:border-box;margin:0;padding:0}
html,body{width:1037px;height:1200px;overflow:hidden;background:var(--white)}
body{font-family:"PT Sans",sans-serif;color:var(--text)}
.page{position:relative;width:1200px;height:1389px;transform:scale(.8642);transform-origin:0 0;overflow:hidden}
.abs{position:absolute}
.hero{left:0;top:0;width:1200px;height:712px;background:linear-gradient(100deg,#b77a3d 0%,#d9c6a8 18%,#c9d2d8 35%,#9aa4a8 48%,#c48a4a 62%,#5f8fcc 78%,#b7874c 100%)}
.hero-band{left:0;top:560px;width:1200px;height:152px;background:linear-gradient(180deg,rgba(60,45,35,0),rgba(40,35,30,.7))}
.header-box{left:124px;top:0;width:960px;height:121px;background:rgba(255,255,255,.55);border-radius:0 0 6px 6px}
.brand{left:160px;top:28px;display:flex;align-items:center;gap:12px;font-family:"PT Sans",sans-serif;font-weight:700;font-size:40px;color:var(--brand-blue)}
.brand-dot{width:34px;height:34px;border-radius:50%;background:var(--green)}
.phone{left:822px;top:12px;display:flex;align-items:center;gap:8px;font-family:"PT Sans Narrow",sans-serif;font-weight:700;font-size:30px;color:var(--brand-blue)}
.search{left:826px;top:64px;width:225px;height:34px;display:flex}
.search-field{flex:1;background:#fff;border:1px solid #d6d6d6;border-radius:3px 0 0 3px;font-size:12px;color:#777;padding:9px 14px}
.search-btn{width:34px;background:var(--deep-blue);display:flex;align-items:center;justify-content:center;border-radius:0 3px 3px 0}
.nav{left:124px;top:155px;width:959px;height:47px;background:var(--nav-blue);display:flex;align-items:center;border-radius:2px}
.nav a{font-family:"PT Sans",sans-serif;font-weight:700;font-size:14px;letter-spacing:.5px;color:#fff;text-decoration:none;padding:0 15.5px;line-height:47px;text-transform:uppercase}
.nav a.active{background:#6cb22e;padding:0 17px 0 25px}
.pricing{left:785px;top:397px;width:303px;height:213px;background:var(--green-panel);border-top:3px solid #fff;padding:14px 18px;color:#fff;font-family:"PT Sans Narrow",sans-serif}
.pricing h2{font-size:25px;font-weight:400;margin-bottom:12px}
.pricing p{font-size:17px;margin:0 0 12px 2px;line-height:22px}
.pill{display:inline-block;background:#fff;color:#333;font-family:"PT Sans Narrow",sans-serif;font-weight:700;font-size:15px;border-radius:14px;padding:3px 19px;margin:6px 0 0 6px}
.rule{left:0;top:712px;width:1200px;height:4px;background:#6cb22e}
.content{left:123px;top:654px;width:967px;height:640px;background:#fff;border-radius:6px 6px 0 0;box-shadow:0 0 6px rgba(0,0,0,.18)}
.h{font-family:"PT Sans Narrow",sans-serif;font-weight:700;font-size:22px;color:var(--green-dark);text-transform:uppercase}
.ph{border-radius:8px;box-shadow:0 1px 3px rgba(0,0,0,.35)}
.about-title{left:390px;top:707px;font-size:14px;font-weight:700;color:#222}
.about-text{left:391px;top:729px;width:341px;font-size:11.5px;line-height:16px;color:var(--muted);text-align:justify}
.btn-blue{left:651px;top:876px;width:80px;height:32px;background:#1e7ad1;color:#fff;font-family:"PT Sans Narrow",sans-serif;font-size:15px;display:flex;align-items:center;justify-content:center;box-shadow:0 1px 2px rgba(0,0,0,.4)}
.service-list{left:793px;top:728px;list-style:none;font-size:13px;color:#333}
.service-list li{height:23px;display:flex;align-items:center;gap:8px}
.service-list li::before{content:"";width:11px;height:11px;background:var(--orange);border-radius:2px}
.estimate{left:794px;top:903px;width:260px;height:329px;background:var(--green);border-radius:12px;box-shadow:0 2px 4px rgba(0,0,0,.3)}
.estimate-head{left:804px;top:912px;width:241px;height:41px;border-bottom:2px solid #4f9a35;display:flex;align-items:center;gap:14px;font-family:"PT Sans Narrow",sans-serif;font-weight:700;font-size:22px;color:#fff}
.field{left:813px;width:221px;height:31px;background:#fff;border:1px solid #d7d7d7;border-radius:3px;font-style:italic;font-size:11.5px;color:#777;padding:8px 15px}
.btn-orange{background:var(--orange);border-radius:13px;color:#222;font-family:"PT Sans Narrow",sans-serif;font-weight:700;font-size:15px;display:flex;align-items:center;justify-content:center;box-shadow:inset 0 -2px 0 var(--orange-dark)}
.submit{left:955px;top:1196px;width:79px;height:28px;color:#fff;font-style:italic;border:2px solid #fff}
.divider{height:10px;background:radial-gradient(ellipse at top,rgba(0,0,0,.09),rgba(0,0,0,0) 70%)}
.rev-name{font-size:13px;color:#222}
.rev-text{font-size:11.5px;line-height:16px;color:var(--muted);width:181px;text-align:justify}
.stars{display:flex;gap:2px}
.tip-text{left:527px;top:1104px;width:224px;font-size:11.5px;line-height:16px;color:var(--muted);text-align:justify}
.footer{left:0;top:1292px;width:1200px;height:97px;background:var(--green);border-top:1px dotted #fff}
.social{left:126px;top:1324px;display:flex;gap:12px}
.social span{width:27px;height:26px;border-radius:2px;box-shadow:0 1px 2px rgba(0,0,0,.35)}
.copy{right:101px;top:1326px;font-size:11px;color:#fff}
</style>
</head>
<body>
<div class="page">
  <div class="abs hero" role="img" aria-label="Photo of a smiling cleaner in a blue shirt wiping a kitchen faucet by a sunny window"></div>
  <div class="abs hero-band"></div>

  <header>
    <div class="abs header-box"></div>
    <div class="abs brand"><span class="brand-dot"></span>Tidy Nest</div>
    <div class="abs phone">
      <svg width="24" height="24" viewBox="0 0 24 24"><path d="M6.6 10.8a15 15 0 0 0 6.6 6.6l2.2-2.2c.3-.3.7-.4 1-.2 1.1.4 2.3.6 3.6.6.6 0 1 .4 1 1V20c0 .6-.4 1-1 1A17 17 0 0 1 3 4c0-.6.4-1 1-1h3.5c.6 0 1 .4 1 1 0 1.3.2 2.5.6 3.6.1.3 0 .7-.2 1z" fill="#5cb447"/></svg>
      289-555-0142
    </div>
    <div class="abs search">
      <div class="search-field">Search</div>
      <div class="search-btn"><svg width="18" height="18" viewBox="0 0 18 18"><circle cx="7" cy="7" r="5" fill="none" stroke="#fff" stroke-width="2"/><path d="M11 11l5 5" stroke="#fff" stroke-width="3" stroke-linecap="round"/></svg></div>
    </div>
    <nav class="abs nav">
      <a class="active">Home</a><a>About us</a><a>Our service</a><a>Photos gallery</a><a>Reviews</a><a>Tips</a><a>FAQ</a><a>Contact us</a><a>Looking for a job?</a>
    </nav>
  </header>

  <svg class="abs" style="left:40px;top:342px" width="30" height="84" viewBox="0 0 30 84"><path d="M26 2L3 42l23 40" fill="none" stroke="#fff" stroke-width="2.5"/></svg>
  <svg class="abs" style="left:1120px;top:342px" width="30" height="84" viewBox="0 0 30 84"><path d="M4 2l23 40L4 82" fill="none" stroke="#fff" stroke-width="2.5"/></svg>

  <section class="abs pricing">
    <h2>PRICING IS.. SIMPLE.</h2>
    <p>$79 FOR HOMES LESS THAN 1000 SQ FT</p>
    <p>$89 FOR HOMES 1000-1800 SQ FT</p>
    <p>$99 FOR HOMES 1800-2600 SQ FT</p>
    <span class="pill">MORE</span>
  </section>

  <div class="abs rule"></div>
  <div class="abs content"></div>

  <h2 class="abs h" style="left:155px;top:682px">About us</h2>
  <div class="abs ph" style="left:158px;top:713px;width:215px;height:149px;background:linear-gradient(135deg,#c9a57c,#e8dccb 50%,#a88a6a)" role="img" aria-label="Photo of a smiling family with two children and a golden dog on a sofa"></div>
  <h3 class="abs about-title">HOUSE CLEANING…TIDY NEST!</h3>
  <div class="abs about-text">
    <p>We are Martin and Elena Kowal and we have personally experienced the struggle of finding a reliable and affordable maid service. We understand how busy life can be and cleaning is one of the tasks that falls off the list when you're stretched too thin. We are here to help! Let Tidy Nest take care of the house cleaning so you can focus on the more important things in life.</p>
    <p style="margin-top:16px">Ashford, Brookvale, Cedarton and Millbank residents can count on us to make your home sparkle from top to bottom!</p>
  </div>
  <div class="abs btn-blue">learn more</div>

  <h2 class="abs h" style="left:788px;top:682px">About service</h2>
  <ul class="abs service-list">
    <li>Thoroughly clean your bathrooms, kitchen</li>
    <li>Bedrooms and living areas</li>
    <li>Mop or vacuum your floors</li>
    <li>Dust surfaces</li>
    <li>Collect garbage</li>
    <li>Make beds</li>
  </ul>

  <form class="abs estimate"></form>
  <div class="abs estimate-head">
    <svg width="40" height="34" viewBox="0 0 40 34"><g transform="rotate(-18 20 17)"><rect x="4" y="7" width="32" height="21" rx="2" fill="#fff" stroke="#ccc"/><path d="M4 8l16 12 16-12" fill="none" stroke="#bbb" stroke-width="1.5"/></g></svg>
    BRIMTALLOW
  </div>
  <div class="abs field" style="top:967px">First Name &amp; Last Name</div>
  <div class="abs field" style="top:1008px">Address, City</div>
  <div class="abs field" style="top:1049px">Email</div>
  <div class="abs field" style="top:1090px">Phone</div>
  <div class="abs field" style="top:1131px;height:54px;padding-top:19px">Comments</div>
  <div class="abs btn-orange submit">SUBMIT</div>

  <h2 class="abs h" style="left:155px;top:959px">Last reviews</h2>
  <div class="abs divider" style="left:150px;top:988px;width:330px"></div>

  <div class="abs ph" style="left:157px;top:1027px;width:101px;height:73px;border-radius:2px;background:linear-gradient(180deg,#7aa6d0,#c7b8a4)" role="img" aria-label="Photo of a couple outdoors in winter"></div>
  <div class="abs" style="left:272px;top:1022px">
    <div class="rev-name">Meet Elena and Martin</div>
    <div class="rev-text" style="margin-top:4px">It's about caring, not just cleaning. Having personally experienced the struggles</div>
  </div>
  <div class="abs stars" style="left:276px;top:1103px">
    <svg width="64" height="12" viewBox="0 0 64 12"><g fill="#f5a300"><path id="st" d="M6 0l1.8 3.8 4.2.4-3.2 2.8 1 4.1L6 9 2.2 11.1l1-4.1L0 4.2l4.2-.4z"/><use href="#st" x="13"/><use href="#st" x="26"/><use href="#st" x="39"/></g><use href="#st" x="52" fill="#aaa"/></svg>
  </div>
  <div class="abs btn-orange" style="left:378px;top:1092px;width:74px;height:26px">More</div>

  <div class="abs ph" style="left:157px;top:1147px;width:101px;height:73px;border-radius:2px;background:linear-gradient(180deg,#a7c28a,#c69a7a)" role="img" aria-label="Photo of two smiling women outdoors"></div>
  <div class="abs" style="left:272px;top:1143px">
    <div class="rev-name">Meet Elena and Martin</div>
    <div class="rev-text" style="margin-top:4px">It's about caring, not just cleaning. Having personally experienced the struggles</div>
  </div>
  <div class="abs stars" style="left:276px;top:1224px">
    <svg width="64" height="12" viewBox="0 0 64 12"><g fill="#f5a300"><use href="#st"/><use href="#st" x="13"/><use href="#st" x="26"/><use href="#st" x="39"/></g><use href="#st" x="52" fill="#aaa"/></svg>
  </div>
  <div class="abs btn-orange" style="left:378px;top:1213px;width:74px;height:26px">More</div>

  <h2 class="abs h" style="left:516px;top:959px">Tip of the week</h2>
  <div class="abs divider" style="left:511px;top:988px;width:250px"></div>
  <div class="abs ph" style="left:523px;top:1018px;width:228px;height:75px;background:linear-gradient(180deg,#dfe8cf,#9ebc6e)" role="img" aria-label="Photo of a group of seniors on a golf course"></div>
  <p class="abs tip-text">Sed ut perspiciatis unde omnis iste natus error sit voluptatem accusantium doloremque laudantium, totam rem aperiam, veritatis et quasi architecto beatae vitaeac-cusantium doloremque laudantium, totam rem aperiam.</p>
  <div class="abs btn-orange" style="left:529px;top:1213px;width:74px;height:26px">More</div>

  <footer class="abs footer"></footer>
  <div class="abs social" aria-label="Social links">
    <span style="background:#3b5b9e"></span>
    <span style="background:#39b3e6"></span>
    <span style="background:#333"></span>
    <span style="background:#f39322"></span>
    <span style="background:#d4211e"></span>
    <span style="background:#8e9aa8"></span>
  </div>
  <div class="abs copy">© 2013 Tidy Nest House Cleaning All rights reserved</div>
</div>
</body>
</html>
```